Agriculture Business Card

I want to use my existing logo and use my tagline of "Don't Guess...Soil Test" on the card. Looking for a double sided card that will really get peoples attention.
Contact Info:
Marlow Field Crop Edge
Calvin Brusk
2917 K Lane
Larkin, NE 68593
402-555-0193
calvin.r.brusk@fieldmailbox.net

```html
<!DOCTYPE html>
<html lang="en">
<head>
<meta charset="utf-8">
<title>Marlow Field Crop Edge — Business Card</title>
<link rel="stylesheet" href="https://fonts.googleapis.com/css2?family=Arimo:wght@400;700&family=Roboto+Condensed:wght@500;700&display=swap">
<style>
  :root {
    --backdrop: #2b2e33;
    --card: #1e1e1e;
    --card-edge: #141414;
    --field-green: #35a944;
    --wheat-gold: #f4a81d;
    --soil-brown: #a9663f;
    --chalk: #e9e9e9;
    --muted-mark: #2c2c2c;
  }
  * { box-sizing: border-box; margin: 0; padding: 0; }
  html, body { width: 1200px; height: 900px; overflow: hidden; }
  body {
    background: var(--backdrop);
    font-family: "Arimo", Arial, sans-serif;
    position: relative;
  }
  .card {
    position: absolute;
    width: 640px;
    height: 366px;
    background: var(--card);
    border-radius: 28px;
    overflow: hidden;
    box-shadow: 0 0 0 1px var(--card-edge);
  }
  .card--front { left: 70px; top: 70px; }
  .card--back { left: 490px; top: 464px; }

  .card__edge-band {
    position: absolute; left: 0; top: 0; bottom: 0;
    width: 12px; background: var(--field-green);
  }

  .brand {
    position: absolute; left: 300px; top: 62px;
    display: flex; align-items: center; gap: 14px;
  }
  .brand__dot {
    width: 54px; height: 54px; border-radius: 50%;
    background: var(--wheat-gold);
  }
  .brand__name {
    font-family: "Roboto Condensed", sans-serif;
    font-weight: 700; font-size: 26px; line-height: 1.05;
    color: var(--soil-brown); width: 190px;
  }

  .person {
    position: absolute; left: 58px; top: 196px;
    text-align: right; width: 210px;
  }
  .person__name {
    font-family: "Roboto Condensed", sans-serif;
    font-weight: 500; font-size: 32px; letter-spacing: 0.5px;
    color: var(--soil-brown); text-transform: uppercase;
  }
  .person__role { font-size: 15px; color: var(--chalk); margin-top: 6px; }

  .divider {
    position: absolute; left: 290px; top: 190px;
    width: 2px; height: 110px; background: #2f5a33;
  }

  .contacts {
    position: absolute; left: 312px; top: 196px;
    list-style: none; display: flex; flex-direction: column; gap: 14px;
  }
  .contacts__item {
    display: flex; align-items: center; gap: 10px;
    font-size: 16px; color: var(--chalk);
  }
  .contacts__icon { width: 16px; height: 16px; flex: none; fill: var(--wheat-gold); }

  .back-mark {
    position: absolute; left: 300px; top: 110px; width: 280px;
    font-family: "Roboto Condensed", sans-serif;
    font-weight: 700; font-size: 40px; line-height: 1.05;
    color: var(--muted-mark);
  }
  .tagline {
    position: absolute; left: 50px; top: 230px;
    font-size: 26px; color: var(--wheat-gold);
  }
</style>
</head>
<body>
  <section class="card card--front" aria-label="Card front">
    <div class="card__edge-band"></div>
    <div class="brand">
      <div class="brand__dot"></div>
      <div class="brand__name">Marlow Field Crop Edge</div>
    </div>
    <div class="person">
      <h1 class="person__name">Calvin Brusk</h1>
      <p class="person__role">CEO/Founder</p>
    </div>
    <div class="divider"></div>
    <ul class="contacts">
      <li class="contacts__item">
        <svg class="contacts__icon" viewBox="0 0 16 16"><path d="M3 1h3l1.5 4-2 1.2a9 9 0 0 0 4.3 4.3L11 8.5l4 1.5v3a2 2 0 0 1-2 2A12 12 0 0 1 1 3a2 2 0 0 1 2-2z"/></svg>
        402-555-0193
      </li>
      <li class="contacts__item">
        <svg class="contacts__icon" viewBox="0 0 16 16"><path d="M1 3h14v10H1z M1.5 3.5 8 9l6.5-5.5" stroke="#1e1e1e" stroke-width="1.2"/></svg>
        calvin.r.brusk@fieldmailbox.net
      </li>
      <li class="contacts__item">
        <svg class="contacts__icon" viewBox="0 0 16 16"><path d="M8 0a5.5 5.5 0 0 0-5.5 5.5C2.5 10 8 16 8 16s5.5-6 5.5-10.5A5.5 5.5 0 0 0 8 0zm0 8a2.5 2.5 0 1 1 0-5 2.5 2.5 0 0 1 0 5z"/></svg>
        2917 K Lane Larkin, NE 68593
      </li>
    </ul>
  </section>

  <section class="card card--back" aria-label="Card back">
    <div class="back-mark">Marlow Field Crop Edge</div>
    <p class="tagline">Don't Guess...Soil Test</p>
  </section>
</body>
</html>
```